Cedar Brook Stables, LLC

Equestrian business card to promote equine retirement, farm sitting, short term board. Located in Willow Creek, SC.
Updates
Updated color schemes.
Contact Information for Business Card
Contact info, description of work.
Colors
0094D4
00A9DD
6FCCEA
C7EBF8
E9F6FB
59FF00
82FF00
B8FF75
E3FFCB
F4FFEA
F0912C
F2A743
F7CA91
FBE8D2
FDF5EE

```html
<!DOCTYPE html>
<html lang="en">
<head>
<meta charset="UTF-8">
<title>Cedar Brook Stables, LLC – Business Card</title>
<link rel="stylesheet" href="https://fonts.googleapis.com/css2?family=Cinzel:wght@600;700&family=Marcellus&display=swap">
<style>
  :root {
    --page-bg: #e4e4e4;
    --card-bg: #ebe7e3;
    --ink: #111111;
    --band-text: #ece8e4;
  }
  * { margin: 0; padding: 0; box-sizing: border-box; }
  html, body {
    width: 1200px;
    height: 900px;
    overflow: hidden;
    background: var(--page-bg);
  }
  .canvas {
    position: relative;
    width: 1200px;
    height: 900px;
  }
  .business-card {
    position: absolute;
    left: 75px;
    top: 150px;
    width: 1050px;
    height: 600px;
    background: var(--card-bg);
    box-shadow: 0 6px 18px rgba(0, 0, 0, 0.12);
    color: var(--ink);
  }
  .company-name {
    position: absolute;
    left: 0;
    right: 0;
    top: 238px;
    text-align: center;
    font-family: "Cinzel", serif;
    font-weight: 700;
    font-size: 44px;
    letter-spacing: 0.5px;
    text-transform: uppercase;
    white-space: nowrap;
  }
  .contact-row {
    position: absolute;
    left: 0;
    right: 0;
    top: 368px;
    display: flex;
    justify-content: center;
    align-items: center;
  }
  .person-name {
    font-family: "Marcellus", serif;
    font-size: 46px;
    letter-spacing: 1.5px;
    padding-right: 26px;
    white-space: nowrap;
  }
  .divider {
    width: 2px;
    height: 82px;
    background: var(--ink);
  }
  .contact-details {
    list-style: none;
    padding-left: 22px;
    font-family: "Marcellus", serif;
    font-size: 31px;
    letter-spacing: 1px;
    line-height: 42px;
    white-space: nowrap;
  }
  .contact-details li {
    display: flex;
    align-items: center;
    gap: 16px;
  }
  .contact-details svg {
    width: 20px;
    height: 22px;
    flex: none;
  }
  .services-band {
    position: absolute;
    left: 0;
    right: 0;
    top: 512px;
    height: 38px;
    background: var(--ink);
    display: flex;
    justify-content: center;
    align-items: center;
    gap: 10px;
    font-family: "Cinzel", serif;
    font-weight: 600;
    font-size: 19px;
    letter-spacing: 1px;
    text-transform: uppercase;
    color: var(--band-text);
    white-space: nowrap;
  }
  .services-band .separator {
    font-size: 11px;
  }
</style>
</head>
<body>
<div class="canvas">
  <section class="business-card">
    <h1 class="company-name">Cedar Brook Stables, LLC</h1>

    <div class="contact-row">
      <p class="person-name">Nora Whitfield</p>
      <div class="divider"></div>
      <ul class="contact-details">
        <li>
          <svg viewBox="0 0 20 22" aria-hidden="true">
            <path d="M10 1a7 7 0 0 0-7 7c0 5 7 13 7 13s7-8 7-13a7 7 0 0 0-7-7z" fill="var(--ink)"/>
            <circle cx="10" cy="8" r="2.6" fill="var(--card-bg)"/>
          </svg>
          <span>Willow Creek, SC</span>
        </li>
        <li>
          <svg viewBox="0 0 20 22" aria-hidden="true">
            <path d="M4 3l3 0 2 5-2 1.5c1 2.5 3 4.5 5.5 5.5L14 13l5 2v3c0 1-1 2-2 2C9 20 2 13 2 5c0-1 1-2 2-2z" fill="none" stroke="var(--ink)" stroke-width="2" stroke-linejoin="round"/>
          </svg>
          <span>803.555.0147</span>
        </li>
      </ul>
    </div>

    <div class="services-band">
      <span>Equine Retirement</span>
      <span class="separator">◆</span>
      <span>Farm Sitting</span>
      <span class="separator">◆</span>
      <span>Short Term Board</span>
    </div>
  </section>
</div>
</body>
</html>
```